Book Cover for a book on Quiet Ventures

I am self-publishing my book on Brindlecart and need a book cover made. Below are the details. See attached templates for size we need to use. I also attached a previous cover we had made that I liked. The problem with it was they were two boys helping each other but the book is about women. I'm open to your ideas on the cover though, but I wanted to show you a style I liked as an idea.
Front of Cover
Book Title: Quiet Ventures
Book Subtitle: Unvarnished Notes of a Woman Founder
Author Name: Lorna T. Pelham
Add on the Spine of Cover: Quiet Ventures and Lorna T. Pelham
Back of the Cover Text:
Quiet Ventures: Unvarnished Notes of a Woman Founder is an honest account of a business owner’s experience attempting to navigate the start-up community while also pursuing spiritual growth. Author Lorna Pelham defines a spiritual entrepreneur as “someone who runs an enterprise with the purpose of growing love rather than material gain.” This book discusses the three dimensions of Quiet Ventures:
1. The business is an integral part of the founder’s spiritual journey.
2. Employees working for the spiritual enterprise, whether they know it or not, encounter this company because it's part of their spiritual path.
3. The business itself has a life force of its own and its purpose is to further the kingdom of heaven on earth.
These three dimensions happen simultaneously and work together to produce the greatest possible result. However, this can feel confusing to a founder juggling these dimensions while also trying to manage and run a business. This is not a formulaic self-help book or roadmap. Rather, it is a compilation of personal reflections that often seem at odds with the traditional world of entrepreneurship.
Below the description add my picture (see attached for my picture)
Bio text:
Lorna Pelham founded Halvex with the vision of ushering in a life-long education system that shifts away from standardization to one that empowers people to live their purpose. In college, Lorna interned for Open Meadow, a women’s empowerment initiative where she recognized her passion for helping people find their voice. Lorna's 20-year journey has come full circle to empowering other female CEOs who are pursuing the path of Quiet Ventures.
NOTE: Please note that Brindlecart puts a bar code on the bottom right of the back cover as is noted on the attached template.
Size template is attached to the brief, here are the sizes typed out:
# Description Width (in) Height (in)
1 Full Cover 12.79 9.25
2 Front Cover 6 9
3 Safe Area 5.875 8.75
4 Bleed 0.125 0.125
5 Margin 0.125 0.125
6 Spine 0.54 9
7 Spine Safe Area 0.415 8.75
8 Spine Margin 0.062 0.062
9 Barcode Margin 0.25 0.25
Pre-publication checklist
BRINDLECART TIPS for the final cover:
1. Save as a PDF. Your cover must be a single PDF that includes the back cover, spine, and front cover as one image.
2. Flatten all transparencies. These can cause the file to print with missing or distorted content. Consult your software's documentation to learn how.
3. Embed your fonts. Consult your software's documentation to learn how.
4. Remove crop marks, color bars, template text. Crop marks are lines showing where pages should be trimmed. Color bars are strips with a series of patches used to ensure color balance during printing. Also, remove any template text, PDF creation guides, or software references.
5. Ensure your cover image meets the minimum resolution of 300 DPI (dots per inch).
6. Optimize PDFs. Optimization is useful to reduce your file size, allowing for higher performance when transferring, uploading, viewing, and printing the files.
7. Remove file security. Locked or encrypted files will fail review.
Target Market(s)
Women who want to be CEOs or are currently CEOs of companies.
Industry/Entity Type
Entrepreneurship, business, spirituality
Requirements
Must have
- Just the text on the description. A very welcoming feel.
Nice to have
- I like the idea of having a sunrise/sunset in the image somehow like in the example I attached to the brief, but again I'm open.
Should not have
- Please don't put any yoga or meditation poses or hands outstretched. I have a lot of interesting ones that look like my example so if you are going to submit after Saturday 10/29, please only do so if you have a new idea! Thanks!

```html
<!DOCTYPE html>
<html lang="en">
<head>
<meta charset="utf-8">
<title>Quiet Ventures — Full Cover</title>
<link href="https://fonts.googleapis.com/css2?family=Graduate&family=Roboto+Slab:wght@400&family=Roboto:wght@400&family=Tinos&display=swap" rel="stylesheet">
<style>
  :root{
    --stage:#1c1c1c;
    --paper:#fffdf7;
    --ink:#231a15;
    --accent:#c9772b;
    --rule:#6b6b6b;
    --text:#222;
  }
  *{margin:0;padding:0;box-sizing:border-box}
  html,body{width:1200px;height:1200px;overflow:hidden;background:var(--stage)}
  .cover{position:absolute;left:63px;top:211px;width:1074px;height:777px;background:var(--paper);overflow:hidden}
  .abs{position:absolute}
  .title-mark{font-family:"Graduate",serif;color:var(--ink);text-align:center;line-height:1;white-space:nowrap}
  .subtitle-mark{font-family:"Roboto Slab",serif;color:var(--accent);text-align:center;line-height:1;letter-spacing:1px;white-space:nowrap}
  .back-title{left:114px;top:41px;width:314px;font-size:89px}
  .back-sub{left:114px;top:125px;width:314px;font-size:27px}
  .copy{font-family:"Tinos",serif;color:var(--text);font-size:13.4px;line-height:16.8px;text-align:justify}
  .blurb{left:34px;top:179px;width:456px}
  .dimensions{list-style:none;margin:9px 0 5px 21px;text-align:left;font-size:13.8px;line-height:18.4px}
  .dimensions li{position:relative;padding-left:10px;margin-bottom:6px;padding-right:20px}
  .dimensions li::before{content:"";position:absolute;left:0;top:7px;width:4px;height:4px;border-radius:50%;background:var(--accent)}
  .author-photo{left:37px;top:492px;width:100px;height:113px;background:linear-gradient(160deg,#7fa66a,#b9c9a0 45%,#e9546a 90%)}
  .bio{left:153px;top:494px;width:339px}
  .front-photo{left:556px;top:0;width:518px;height:433px;background:radial-gradient(ellipse at 50% 55%,#f4efe4 0%,#cdbfa8 40%,#6d5e4e 75%,#2b241e 100%)}
  .front-band{left:553px;top:433px;width:521px;height:173px;background:var(--ink)}
  .front-title{left:0;top:8px;width:521px;font-size:123px;color:var(--paper)}
  .front-sub{left:0;top:119px;width:521px;font-size:38px}
  .tagline{left:556px;top:613px;width:518px;font-family:"Roboto",sans-serif;font-size:25px;letter-spacing:5.5px;text-align:center;color:var(--ink);line-height:30px;white-space:nowrap}
  .author{left:556px;top:680px;width:518px;font-family:"Tinos",serif;font-size:46px;text-align:center;color:var(--ink);white-space:nowrap}
</style>
</head>
<body>
<div class="cover">
  <!-- Back cover -->
  <div class="abs title-mark back-title">QUIET</div>
  <svg class="abs" style="left:0;top:0" width="553" height="180" aria-hidden="true">
    <line x1="128" y1="140" x2="193" y2="140" stroke="var(--accent)" stroke-width="2"/>
    <line x1="349" y1="140" x2="414" y2="140" stroke="var(--accent)" stroke-width="2"/>
    <line x1="70" y1="162" x2="440" y2="162" stroke="var(--rule)" stroke-width="1.5"/>
  </svg>
  <div class="abs subtitle-mark back-sub">VENTURES</div>

  <div class="abs copy blurb">
    <p>Unvarnished Notes of a Woman Founder is an honest account of a business owner’s experience attempting to navigate the start-up community while also pursuing spiritual growth. Author Lorna Pelham defines a spiritual entrepreneur as “someone who runs an enterprise with the purpose of growing love rather than material gain.” This book discusses the three dimensions of Quiet Ventures:</p>
    <ul class="dimensions">
      <li>The business is an integral part of the founder’s spiritual journey.</li>
      <li>Employees working for the spiritual enterprise, whether they know it or not, encounter this company because it's part of their spiritual</li>
      <li>The business itself has a life force of its own and its purpose is to further the kingdom of heaven on earth.</li>
    </ul>
    <p>These three dimensions happen simultaneously and work together to produce the greatest possible result. However, this can feel confusing to a founder juggling these dimensions while also trying to manage and run a business. This is not a formulaic self-help book or roadmap. Rather, it is a compilation of personal reflections that often seem at odds with the traditional world of entrepreneurship.</p>
  </div>

  <div class="abs author-photo" role="img" aria-label="Portrait photo of the author"></div>
  <p class="abs copy bio">Lorna Pelham founded Halvex with the vision of ushering in a life-long education system that shifts away from standardization to one that empowers people to live their purpose. In college, Lorna interned for Open Meadow, a women’s empowerment initiative where she recognized her passion for helping people find their voice. Lorna's 20-year journey has come full circle to empowering other female CEOs who are pursuing the path of Quiet Ventures.</p>

  <!-- Spine -->
  <svg class="abs" style="left:516px;top:0" width="40" height="777" aria-label="Spine: Quiet Ventures, Lorna T. Pelham">
    <g transform="translate(12,62) rotate(90)">
      <text x="0" y="0" font-family="Graduate, serif" font-size="30" fill="var(--ink)">QUIET</text>
      <text x="112" y="0" font-family="Roboto Slab, serif" font-size="30" fill="var(--accent)">VENTURES</text>
      <text x="440" y="0" font-family="Tinos, serif" font-size="32" fill="var(--ink)">Lorna T. Pelham</text>
    </g>
  </svg>

  <!-- Front cover -->
  <div class="abs front-photo" role="img" aria-label="Sepia photo of many hands joined together in a circle"></div>
  <div class="abs front-band">
    <div class="abs title-mark front-title">QUIET</div>
    <svg class="abs" style="left:0;top:0" width="521" height="173" aria-hidden="true">
      <line x1="55" y1="143" x2="158" y2="143" stroke="var(--accent)" stroke-width="2"/>
      <line x1="363" y1="143" x2="466" y2="143" stroke="var(--accent)" stroke-width="2"/>
    </svg>
    <div class="abs subtitle-mark front-sub">VENTURES</div>
  </div>
  <div class="abs tagline">UNVARNISHED NOTES OF<br>A WOMAN FOUNDER</div>
  <div class="abs author">Lorna T. Pelham</div>
</div>
</body>
</html>
```